Inspiring Fundraising Foundation Website to Provide Academic Scholarships

Hello, we are launching a foundation to provide academic scholarships to high school students for college. We'd like this to be an informational website with contact information. There will be a total of approximately 5-7 pages in all.
The color scheme will be purple and white, with a girly feel. I 've attached the logo for reference!

Target Market(s)

high school students, college students

Industry/Entity Type

Education

Coding

Coded - Design and coding required

Number of Pages Required

5+ page

Font styles to use
Serif
Sans Serif
Script

Colors
6b449b
886aae
b7a5cd
e4daeb
ffffff
fdf9cf
fbf289

Requirements
Must have
• Purple, girly feel, to reflect the logo's style. Should be light-themed
Should not have
• No dark themes (aka heavy on black or dark colors)

```html
<!DOCTYPE html>
<html lang="en">
<head>
<meta charset="utf-8">
<title>Elena Marquez Foundation</title>
<link href="https://fonts.googleapis.com/css2?family=Lato:wght@300;400;700;900&display=swap" rel="stylesheet">
<style>
:root{
  --purple-deep:#3d1a5b;
  --purple:#6b449b;
  --purple-mid:#886aae;
  --lilac:#b7a5cd;
  --lilac-pale:#e4daeb;
  --white:#ffffff;
  --cream:#fdf9cf;
  --yellow:#fbf289;
  --hero-bg:#cfd7dd;
  --ink:#333333;
  --body-text:#5a5a5a;
  --footer:#2f2f2f;
  --footer-text:#cfcfcf;
  --field:#f6eef0;
}
*{box-sizing:border-box;margin:0;padding:0}
html,body{width:1200px;height:3041px;overflow:hidden}
body{position:relative;font-family:'Lato',sans-serif;color:var(--ink);background:var(--white)}
.abs{position:absolute}

/* header */
.hero{left:0;top:0;width:1200px;height:610px;background:linear-gradient(90deg,#d9dfe3,var(--hero-bg))}
.site-header{left:85px;top:0;width:1028px;height:122px;background:rgba(255,255,255,.96)}
.topbar{left:548px;top:0;width:565px;height:44px;background:var(--purple-deep);clip-path:polygon(30px 0,100% 0,100% 100%,0 100%);color:var(--white);font-size:14px;display:flex;align-items:center;gap:26px;padding-left:50px}
.topbar .socials{display:flex;gap:12px;margin-left:8px}
.topbar .socials span{width:12px;height:12px;background:var(--white);border-radius:50%}
.logo{left:105px;top:22px;width:120px;color:var(--purple);font-size:22px;font-weight:700;line-height:1}
.logo .mark{display:block;width:26px;height:26px;border-radius:50%;background:var(--purple);margin:0 0 6px 30px}
.main-nav{left:381px;top:70px;display:flex;gap:22px;font-size:14px;font-weight:700;color:#222}
.main-nav a{color:inherit;text-decoration:none;padding-bottom:9px}
.main-nav a.active{border-bottom:2px solid var(--purple-deep)}

.hero-photo{left:735px;top:60px;width:330px;height:520px;border-radius:160px 160px 0 0;background:linear-gradient(180deg,#c7b49f,#6b86a8 55%,#557198)}
.hero-arrow{width:44px;height:44px;border:2px solid rgba(255,255,255,.85);border-radius:50%}
.hero-title{left:132px;top:254px;color:var(--purple-deep)}
.hero-title .pre{font-size:40px;font-weight:300;letter-spacing:1px;display:block;line-height:1.1}
.hero-title .name{font-size:40px;font-weight:900;display:block;line-height:1.1}
.hero-lede{left:132px;top:348px;width:650px;font-size:18px;line-height:1.3;color:#3a3a3a}
.btn{display:inline-flex;align-items:center;justify-content:center;font-size:16px;font-weight:700;text-decoration:none}
.btn-apply-hero{left:132px;top:422px;width:172px;height:43px;background:var(--white);color:#222}
.btn-donate{left:316px;top:422px;width:174px;height:43px;background:var(--yellow);color:#222}
.hero-wave{left:0;top:530px}

/* about */
.about-photo{left:85px;top:685px;width:345px;height:467px;background:linear-gradient(160deg,#efefef,#d8d2cf 45%,#b8343a 70%,#3b2a2a)}
.about-title{left:460px;top:680px;color:var(--ink);font-size:30px;line-height:1.15}
.about-title .name{font-weight:700;display:block}
.about-copy{left:460px;top:768px;width:650px;font-size:13px;line-height:1.6;color:var(--body-text)}
.about-copy p+p{margin-top:20px}
.btn-dark{background:var(--purple-deep);color:var(--white);font-size:16px}
.btn-read{left:460px;top:1088px;width:152px;height:49px}

/* programs */
.programs{left:0;top:1230px;width:1200px;height:550px;background:var(--purple-deep)}
.section-title{width:1200px;left:0;text-align:center;color:var(--white);font-size:28px;font-weight:400;letter-spacing:1px}
.section-title b{font-weight:700}
.section-sub{left:200px;width:800px;text-align:center;color:var(--white);font-size:12.5px;line-height:1.6}
.program{width:240px;text-align:center}
.program .ring{width:194px;height:194px;margin:0 auto;border-radius:50%;border:6px solid var(--white);padding:7px}
.program .disc{width:100%;height:100%;border-radius:50%;background:var(--white);display:flex;align-items:center;justify-content:center}
.program.featured .disc{background:var(--yellow)}
.program .label{margin-top:22px;color:var(--white);font-size:17px;font-weight:700;text-transform:uppercase}
.program.featured .label{color:var(--yellow)}

/* scholarships */
.scholar-card{left:63px;top:1739px;width:1074px;height:566px;background:var(--white)}
.scholar-photo{left:120px;top:1780px;width:960px;height:525px;background:linear-gradient(180deg,#ffffff 0%,#d9c2b0 20%,#8c7a78 45%,#a5aeb9 70%,#e9e9e9 100%)}
.scholar-banner{left:178px;top:2037px;width:835px;height:268px;background:linear-gradient(180deg,#fbfbfb,#ececec)}
.scholar-title{left:272px;top:2084px;font-size:28px;font-weight:700;color:#1e1e1e}
.scholar-copy{left:272px;top:2134px;width:650px;font-size:13px;line-height:1.65;color:#222}
.btn-apply{left:272px;top:2217px;width:146px;height:41px;font-size:16px}

/* sponsors */
.sponsors{left:0;top:2305px;width:1200px;height:371px;background:var(--purple-deep)}
.sponsor{top:2445px;width:235px;height:115px;background:var(--white);display:flex;align-items:center;justify-content:center;gap:10px;color:#444;font-size:30px;font-weight:700}
.sponsor .dot{width:34px;height:34px;background:#777;border-radius:50%}
.pager{left:548px;top:2619px;display:flex;gap:10px}
.pager span{width:18px;height:18px;border:2px solid var(--white);border-radius:50%}
.pager span.on{background:radial-gradient(circle,var(--white) 40%,transparent 45%)}

/* footer */
.site-footer{left:0;top:2676px;width:1200px;height:365px;background:var(--footer)}
.footer-head{top:2714px;color:var(--white);font-size:15px;padding-bottom:8px;border-bottom:1px solid #888;width:190px;text-transform:uppercase}
.contact-list{left:85px;top:2752px;width:300px;color:var(--footer-text);font-size:12px;line-height:1.5;list-style:none}
.contact-list li{display:flex;gap:14px;margin-bottom:12px}
.contact-list svg{flex:none;margin-top:2px}
.social-row{left:88px;top:2894px;display:flex;gap:10px}
.social-row span{width:26px;height:26px;border-radius:50%}
.quick-links{top:2750px;list-style:none;color:var(--footer-text);font-size:12px;line-height:26px}
.quick-links li::before{content:"»";margin-right:12px}
.form-field{background:var(--field);height:34px;color:#888;font-size:11px;padding:9px 10px}
.btn-send{left:797px;top:2945px;width:152px;height:34px;font-size:13px;font-weight:400}
.footer-rule{left:85px;top:2985px;width:1028px;height:1px;background:#444}
.copyright{left:85px;top:2995px;color:var(--footer-text);font-size:12px}
</style>
</head>
<body>

<section class="hero abs" aria-label="Welcome"></section>
<div class="hero-photo abs" role="img" aria-label="Photo of a smiling student in a denim jacket holding notebooks"></div>
<div class="hero-arrow abs" style="left:43px;top:316px"><svg width="40" height="40"><path d="M23 13 l-7 7 7 7" fill="none" stroke="#fff" stroke-width="2"/></svg></div>
<div class="hero-arrow abs" style="left:1113px;top:316px"><svg width="40" height="40"><path d="M17 13 l7 7 -7 7" fill="none" stroke="#fff" stroke-width="2"/></svg></div>

<header>
  <div class="site-header abs"></div>
  <div class="topbar abs">
    <span>&#9742; - (123) 456 - 789</span>
    <span>&#9993; - info@elenamarquezfoundation.org</span>
    <span class="socials"><span></span><span></span><span></span><span></span></span>
  </div>
  <div class="logo abs"><span class="mark"></span>Elena Marquez Foundation</div>
  <nav class="main-nav abs">
    <a class="active">HOME</a><a>ABOUT US</a><a>PROGRAMS</a><a>GET INVOLVED</a><a>RESOURCES</a><a>NEWS &amp; EVENTS</a><a>CONTACT US</a>
  </nav>
</header>

<h1 class="hero-title abs"><span class="pre">WELCOME TO</span><span class="name">ELENA MARQUEZ FOUNDATION</span></h1>
<p class="hero-lede abs">Lorem ipsum dolor sit amet, consectetur adipiscing elit, sed do eiusmod tempor incididunt ut labore et dolore magna aliqua. Ut enim ad minim veniam.</p>
<a class="btn btn-apply-hero abs">APPLY NOW</a>
<a class="btn btn-donate abs">DONATE NOW</a>
<svg class="hero-wave abs" width="1200" height="82" viewBox="0 0 1200 82">
  <path d="M0 40 C150 20 300 10 450 30 C530 42 560 70 620 66 C700 60 760 30 860 22 C980 14 1100 10 1200 0 L1200 82 L0 82Z" fill="#3d1a5b"/>
  <path d="M0 70 C160 36 330 34 460 52 C540 64 570 80 620 80 C700 78 760 50 870 42 C990 34 1110 34 1200 40 L1200 82 L0 82Z" fill="#fff"/>
</svg>

<section aria-label="About">
  <div class="about-photo abs" role="img" aria-label="Portrait of the foundation's namesake seated on a red leather sofa"></div>
  <h2 class="about-title abs">ABOUT<span class="name">ELENA MARQUEZ FOUNDATION</span></h2>
  <div class="about-copy abs">
    <p>The Elena Marquez Foundation is dedicated to helping Houston young men and women reach their goal of starting a real estate career. Our foundation will work to make a difference by offering scholarships and internships for future agents.</p>
    <p>Elena Marquez was a significant contributor to the beginning of Reed and Company Properties. As one of the company's first employees, her plan was to work as an Administrative Assistant while she finished her undergraduate degree in Business Administration at Bayview University. With plans to graduate in December of 2016, she couldn't wait to begin her real estate career, since she had just obtained her Real Estate license in 2014. However, on January 23rd, 2015, she was heading home from the Grand Opening party for Reed and Co. Properties when she was struck by a drunk driver and killed at the scene. Sudden and unexpected, her death came too soon and is still grieved by many. From the grief, an idea was born. The Elena Marquez foundation will work to make a difference by not only offering scholarships and internships for future agents but by taking a stand against drinking and driving, an issue that takes thousands of lives each year.</p>
  </div>
  <a class="btn btn-dark btn-read abs">Read More</a>
</section>

<section class="programs abs" aria-label="Our programs"></section>
<h2 class="section-title abs" style="top:1274px">OUR <b>PROGRAMS</b></h2>
<p class="section-sub abs" style="top:1322px">The foundation will award scholarships to two hard working juniors or seniors in college per year. To be eligible, applicants must send their resume and a 1-2 page essay stating why they are passionate in real estate and what they hope to achieve.</p>

<div class="program abs" style="left:123px;top:1433px">
  <div class="ring"><div class="disc">
    <svg width="80" height="80" viewBox="0 0 80 80" fill="#666"><circle cx="40" cy="16" r="8"/><rect x="32" y="26" width="16" height="40" rx="4"/><circle cx="16" cy="28" r="6"/><rect x="10" y="36" width="12" height="30" rx="3"/><circle cx="64" cy="28" r="6"/><rect x="58" y="36" width="12" height="30" rx="3"/></svg>
  </div></div>
  <div class="label">Grants</div>
</div>
<div class="program featured abs" style="left:482px;top:1433px">
  <div class="ring"><div class="disc">
    <svg width="80" height="80" viewBox="0 0 80 80" fill="#3d1a5b"><path d="M40 8 L52 18 L28 18Z"/><rect x="26" y="18" width="28" height="16"/><rect x="8" y="34" width="64" height="34"/><rect x="35" y="52" width="10" height="16" fill="#fbf289"/><rect x="14" y="42" width="8" height="8" fill="#fbf289"/><rect x="58" y="42" width="8" height="8" fill="#fbf289"/></svg>
  </div></div>
  <div class="label">School Scholarships</div>
</div>
<div class="program abs" style="left:839px;top:1433px">
  <div class="ring"><div class="disc">
    <svg width="84" height="80" viewBox="0 0 84 80" fill="#666"><path d="M42 14 L80 32 L42 50 L4 32Z"/><path d="M20 42 V58 C30 66 54 66 64 58 V42 L42 53Z"/><rect x="74" y="32" width="3" height="24"/></svg>
  </div></div>
  <div class="label">College Scholarships</div>
</div>

<section aria-label="Get your scholarships">
  <div class="scholar-card abs"></div>
  <div class="scholar-photo abs" role="img" aria-label="Group of smiling students standing behind a blank banner"></div>
  <div class="scholar-banner abs"></div>
  <h2 class="scholar-title abs">GET YOUR SCHOLARSHIPS</h2>
  <p class="scholar-copy abs">The foundation will award scholarships to two hard working juniors or seniors in college per year. To be eligible, applicants must send their resume and a 1-2 page essay stating why they are passionate in real estate and what they hope to achieve. Application will open February 20th, 2017 and close May 1st, 2017.</p>
  <a class="btn btn-dark btn-apply abs">APPLY NOW</a>
</section>

<section class="sponsors abs" aria-label="Our sponsors"></section>
<h2 class="section-title abs" style="top:2334px">OUR SPONSORS</h2>
<p class="section-sub abs" style="top:2381px">The foundation will award scholarships to two hard working juniors or seniors in college per year.</p>
<div class="sponsor abs" style="left:87px">Northpeak<span class="dot"></span></div>
<div class="sponsor abs" style="left:351px"><span class="dot"></span>Brightlane</div>
<div class="sponsor abs" style="left:614px">Solvane</div>
<div class="sponsor abs" style="left:878px"><span class="dot"></span>Tunewell</div>
<div class="pager abs"><span></span><span class="on"></span><span></span></div>

<footer>
  <div class="site-footer abs"></div>
  <h3 class="footer-head abs" style="left:85px">Contact Us</h3>
  <ul class="contact-list abs">
    <li><svg width="10" height="14" viewBox="0 0 10 14"><path d="M5 0a5 5 0 0 1 5 5c0 4-5 9-5 9S0 9 0 5a5 5 0 0 1 5-5z" fill="#ddd"/><circle cx="5" cy="5" r="2" fill="#2f2f2f"/></svg><span>1420 Linden Avenue, Fairhaven,<br>North Carolina, 27590.</span></li>
    <li><svg width="12" height="12" viewBox="0 0 12 12"><path d="M2 0l3 3-1.5 1.5a7 7 0 0 0 4 4L9 7l3 3-2 2C5 12 0 7 0 2z" fill="#ddd"/></svg><span>(123) 456-7890</span></li>
    <li><svg width="12" height="10" viewBox="0 0 12 10"><rect width="12" height="10" fill="#ddd"/><path d="M0 0l6 5 6-5" fill="none" stroke="#2f2f2f"/></svg><span>info@elenamarquezfoundation.org</span></li>
  </ul>
  <div class="social-row abs"><span style="background:#3b5998"></span><span style="background:#1da1f2"></span><span style="background:#0077b5"></span><span style="background:#dd4b39"></span></div>

  <h3 class="footer-head abs" style="left:442px">Quick Link</h3>
  <ul class="quick-links abs" style="left:442px"><li>Home</li><li>About Us</li><li>Programs</li><li>Get Involved</li></ul>
  <ul class="quick-links abs" style="left:582px"><li>Resources</li><li>News &amp; Events</li><li>Offices</li><li>Contact</li></ul>

  <h3 class="footer-head abs" style="left:797px;width:316px">Leave Message</h3>
  <div class="form-field abs" style="left:797px;top:2750px;width:316px">Name</div>
  <div class="form-field abs" style="left:797px;top:2794px;width:153px">Email</div>
  <div class="form-field abs" style="left:960px;top:2794px;width:153px">Phone</div>
  <div class="form-field abs" style="left:797px;top:2838px;width:316px;height:92px">Subject</div>
  <a class="btn btn-dark btn-send abs" style="background:var(--purple-deep)">SEND NOW</a>

  <div class="footer-rule abs"></div>
  <p class="copyright abs">Copyright &copy; 2017 Elena Marquez Foundation All rights reserved.</p>
</footer>

</body>
</html>
```